Business Card for Industrial Distributor

We need a business card design for an industrial distributor. We sell machine parts for the manufacturing and oil industry. We would like the cards to look clean and modern but with a touch of industry.

Our colors are blue/white.

Please feel free to visit our website www.korvelpartsco.com

Target Market(s)

mexican manufacturers in the automobile/aerospace industry

Industry/Entity Type

Industrial

Colors
ffffff
0555a3

```html
<!DOCTYPE html>
<html lang="en">
<head>
<meta charset="utf-8">
<title>Korvel Parts Co. — Business Card</title>
<link rel="stylesheet" href="https://fonts.googleapis.com/css2?family=Montserrat:wght@400;500;700;800&display=swap">
<style>
  :root {
    --stage: #3a3a3c;
    --card: #050505;
    --blue: #0555a3;
    --blue-bright: #1a7fd4;
    --blue-name: #2a48b8;
    --white: #ffffff;
    --muted: #e6e6e6;
    --rule: #bfbfbf;
  }
  * { margin: 0; padding: 0; box-sizing: border-box; }
  html, body {
    width: 1200px; height: 900px; overflow: hidden;
    background: var(--stage);
    font-family: "Montserrat", Arial, sans-serif;
  }
  .canvas { position: relative; width: 1200px; height: 900px; }
  .card {
    position: absolute; width: 620px; height: 354px;
    background: var(--card); border-radius: 22px; overflow: hidden;
    box-shadow: 0 18px 40px rgba(0,0,0,.45);
  }
  .card--front { left: 110px; top: 80px; }
  .card--back  { left: 470px; top: 466px; }

  /* front */
  .front-mark {
    position: absolute; left: 0; right: 0; top: 70px;
    display: flex; align-items: center; justify-content: center; gap: 22px;
  }
  .front-mark__dot { width: 110px; height: 110px; border-radius: 50%; background: var(--blue); }
  .front-mark__name { font-weight: 800; font-size: 54px; color: var(--blue-name); letter-spacing: .5px; }
  .front-web {
    position: absolute; left: 0; right: 0; bottom: 60px; text-align: center;
    font-size: 19px; color: var(--white); font-weight: 500;
  }
  .front-web .accent { color: var(--blue-bright); }

  /* back */
  .brand {
    position: absolute; left: 60px; top: 210px;
    display: flex; align-items: center; gap: 14px;
  }
  .brand__dot { width: 50px; height: 50px; border-radius: 50%; background: var(--blue); }
  .brand__name { font-weight: 800; font-size: 44px; color: var(--blue-name); }
  .divider {
    position: absolute; left: 350px; top: 60px; width: 1.5px; height: 160px;
    background: linear-gradient(var(--rule), rgba(191,191,191,.3));
  }
  .tab {
    position: absolute; right: 0; top: 0; width: 34px; height: 200px;
    background: var(--blue-bright); border-radius: 0 22px 0 28px;
  }
  .contact { position: absolute; left: 372px; top: 52px; color: var(--white); }
  .contact__name { font-size: 22px; font-weight: 700; color: var(--blue-bright); line-height: 1.1; }
  .contact__role { font-size: 14px; color: var(--muted); margin-bottom: 10px; }
  .contact__addr { font-size: 14px; line-height: 1.4; color: var(--muted); margin-bottom: 8px; }
  .contact__list { list-style: none; font-size: 14px; line-height: 1.5; color: var(--muted); }
  .contact__list li { display: flex; align-items: center; gap: 8px; }
  .contact__list svg { width: 11px; height: 11px; flex: none; }
  .contact__list .accent { color: var(--blue-bright); }
</style>
</head>
<body>
<main class="canvas">
  <section class="card card--front" aria-label="Card front">
    <div class="front-mark">
      <span class="front-mark__dot"></span>
      <span class="front-mark__name">Korvel</span>
    </div>
    <p class="front-web">www.<span class="accent">korvelpartsco</span>.com</p>
  </section>

  <section class="card card--back" aria-label="Card back">
    <div class="tab"></div>
    <div class="brand">
      <span class="brand__dot"></span>
      <span class="brand__name">Korvel</span>
    </div>
    <div class="divider"></div>
    <div class="contact">
      <p class="contact__name">Marten Osley</p>
      <p class="contact__role">Director</p>
      <p class="contact__addr">P.O. Box 4870<br>Lakemont, OH 44012</p>
      <ul class="contact__list">
        <li>
          <svg viewBox="0 0 12 12"><path d="M2 1h3l1 3-1.5 1a7 7 0 0 0 2.5 2.5L8 6l3 1v3a1 1 0 0 1-1 1C5 11 1 7 1 2a1 1 0 0 1 1-1z" fill="#1a7fd4"/></svg>
          +1 555 0142-3381
        </li>
        <li>
          <svg viewBox="0 0 12 12"><rect x="1" y="2.5" width="10" height="7" fill="none" stroke="#1a7fd4" stroke-width="1.2"/><path d="M1 2.5l5 4 5-4" fill="none" stroke="#1a7fd4" stroke-width="1.2"/></svg>
          info@korvelpartsco.com
        </li>
        <li>
          <svg viewBox="0 0 12 12"><circle cx="6" cy="6" r="5" fill="none" stroke="#1a7fd4" stroke-width="1.2"/><path d="M1 6h10M6 1c-2.5 3-2.5 7 0 10M6 1c2.5 3 2.5 7 0 10" fill="none" stroke="#1a7fd4" stroke-width="1"/></svg>
          <span>www.<span class="accent">korvelpartsco</span>.com</span>
        </li>
      </ul>
    </div>
  </section>
</main>
</body>
</html>
```